4747 5858

Web(re)design of an existing directory search site www.le5858.be (in Dutch www.de4747.be and in English www.3838.be).

This site is a directory site, i.e. a "white pages" site whereby people can search the phone & details of another person based on a combination of name + city (for instance smith in Brussels); one can also search a company also based on a combination of name + city (for instance Vornak in Brussels); last but not least one can also search the name of the subscriber behind a specific telephone number (also called reverse search).

This site is quite outdated and needs a redesign, see instructions.

We need the output in XD format.

```html
<!DOCTYPE html>
<html lang="fr">
<head>
<meta charset="utf-8">
<title>Les Renseignements CINQUANTE-HUIT Utiles</title>
<link href="https://fonts.googleapis.com/css2?family=Roboto+Condensed:wght@300;400;700&family=Roboto:wght@400&display=swap" rel="stylesheet">
<style>
  :root {
    --red: #d7141c;
    --red-dark: #b70d14;
    --ink: #333333;
    --muted: #555555;
    --line: #d9d9d9;
    --field-border: #cfcfcf;
    --white: #ffffff;
    --faint: #efefef;
    --captcha-bg: #f9f9f9;
  }
  * { box-sizing: border-box; margin: 0; padding: 0; }
  html, body { width: 1200px; height: 600px; overflow: hidden; background: var(--white); }
  body { font-family: "Roboto Condensed", Arial, sans-serif; color: var(--ink); position: relative; }

  .site-header { position: absolute; left: 0; top: 0; width: 1200px; height: 128px; }
  .brand { position: absolute; left: 24px; top: 38px; display: flex; align-items: center; gap: 8px; }
  .brand-dot { width: 22px; height: 22px; border-radius: 50%; background: var(--red); }
  .brand-name { font-size: 34px; font-weight: 700; color: var(--red); letter-spacing: 1px; }
  .site-title { position: absolute; left: 0; right: 0; top: 40px; text-align: center; font-size: 36px; font-weight: 400; color: var(--ink); }
  .site-title em { font-style: normal; color: var(--red); }
  .lang { position: absolute; left: 1098px; top: 52px; font-size: 18px; color: var(--ink); }
  .lang small { font-size: 11px; margin-left: 2px; }
  .menu-toggle { position: absolute; left: 1155px; top: 56px; width: 23px; }
  .menu-toggle span { display: block; height: 2px; background: var(--ink); margin-bottom: 5px; }

  .main-nav { position: absolute; left: 0; top: 128px; width: 1200px; height: 50px;
    background: linear-gradient(180deg, var(--red) 0%, var(--red-dark) 100%);
    display: flex; justify-content: center; align-items: center; }
  .main-nav a { color: var(--white); text-decoration: none; font-size: 20px; }
  .main-nav .sep { color: var(--white); font-size: 18px; margin: 0 23px; }
  .nav-pointer { position: absolute; left: 380px; top: 181px; }

  .search-form { position: absolute; left: 0; top: 0; width: 1200px; height: 515px; }
  .field { position: absolute; top: 224px; width: 262px; text-align: center; }
  .field label { display: block; font-size: 17px; font-weight: 700; height: 30px; }
  .field .input { height: 42px; border: 1px solid var(--field-border); border-radius: 21px; background: var(--white); }
  .field .hint { margin-top: 10px; font-size: 12px; font-weight: 300; color: var(--muted); }
  .field-name { left: 173px; }
  .field-first { left: 469px; }
  .field-city { left: 764px; }

  .captcha { position: absolute; left: 488px; top: 347px; width: 224px; height: 54px;
    background: var(--captcha-bg); border: 1px solid #ececec; border-radius: 2px;
    font-family: "Roboto", Arial, sans-serif; }
  .captcha .box { position: absolute; left: 9px; top: 16px; width: 20px; height: 20px; border: 2px solid #c1c1c1; border-radius: 2px; background: var(--white); }
  .captcha .label { position: absolute; left: 38px; top: 20px; font-size: 10.5px; color: #222; }
  .captcha .mark { position: absolute; left: 184px; top: 8px; width: 20px; height: 20px; background: #c8ccd3; border-radius: 3px; }
  .captcha .service { position: absolute; right: 7px; top: 34px; font-size: 7px; color: #555; text-align: center; line-height: 1.35; }

  .submit { position: absolute; left: 540px; top: 427px; width: 120px; height: 42px; border-radius: 21px;
    background: linear-gradient(180deg, var(--red) 0%, var(--red-dark) 100%); color: var(--white);
    font-size: 20px; font-weight: 700; display: flex; align-items: center; justify-content: center; }

  .watermark { position: absolute; left: 1005px; top: 336px; width: 175px; height: 155px; display: flex; align-items: center; justify-content: center; gap: 8px; }
  .watermark .dot { width: 34px; height: 34px; border-radius: 50%; background: var(--faint); }
  .watermark .name { font-size: 58px; font-weight: 700; color: var(--faint); }

  .site-footer { position: absolute; left: 0; top: 514px; width: 1200px; height: 86px; border-top: 1px solid var(--line); }
  .footer-links { position: absolute; left: 171px; top: 22px; font-size: 14px; font-weight: 300; color: var(--ink); }
  .footer-links .sep { color: var(--line); margin: 0 8px; }
  .copyright { position: absolute; left: 171px; top: 44px; font-size: 14px; font-weight: 300; color: var(--ink); }
  .partner-badge { position: absolute; left: 940px; top: 18px; width: 60px; height: 50px; border-radius: 6px; background: var(--faint); }
</style>
</head>
<body>
  <header class="site-header">
    <div class="brand"><span class="brand-dot"></span><span class="brand-name">5858</span></div>
    <h1 class="site-title">Les Renseignements <em>CINQUANTE-HUIT</em> Utiles</h1>
    <div class="lang">FR<small>&#8964;</small></div>
    <div class="menu-toggle"><span></span><span></span><span></span></div>
  </header>

  <nav class="main-nav">
    <a href="#">Particuliers</a><span class="sep">|</span>
    <a href="#">Sociétés</a><span class="sep">|</span>
    <a href="#">Annuaire inversé</a><span class="sep">|</span>
    <a href="#">International</a>
  </nav>
  <svg class="nav-pointer" width="22" height="12" viewBox="0 0 22 12" aria-hidden="true"><polygon points="0,0 22,0 11,12" fill="#d7141c"/></svg>

  <div class="watermark" role="img" aria-label="Faint brand name decoration"><span class="dot"></span><span class="name">5858</span></div>

  <form class="search-form">
    <div class="field field-name"><label>Nom de famille:</label><div class="input"></div><p class="hint">Ex: Dupont, Janssens, ...</p></div>
    <div class="field field-first"><label>Prénom:</label><div class="input"></div><p class="hint">Ex: Jan, Louis, ...</p></div>
    <div class="field field-city"><label>Localité:</label><div class="input"></div><p class="hint">Ex: Liége, Anvers, 1150, ....</p></div>

    <div class="captcha">
      <span class="box"></span>
      <span class="label">I'm not a robot</span>
      <span class="mark"></span>
      <span class="service">VerifyBox<br>Privacy - Terms</span>
    </div>

    <div class="submit">58-58!</div>
  </form>

  <footer class="site-footer">
    <div class="footer-links">B2B Services<span class="sep">|</span>Aide<span class="sep">|</span>Conditions générales d'utilisation<span class="sep">|</span>Respect de la vie privée</div>
    <div class="copyright">Copyright Norvela 2022, tous droits réservés.</div>
    <div class="partner-badge" role="img" aria-label="Partner badge"></div>
  </footer>
</body>
</html>
```